Visitenkarten-Design für virtuelle Jobmesse & Jobbörse für Soldaten
Zielgruppe
Die KVL GmbH ist ein Unternehmen das zwei Hauptprodukte betreibt! Zum einen Jobbörse für Soldaten unter www.laufbahnwechsel-beispiel.de und zum anderen eine virtuelle Jobmesse für Soldaten unter www.merivon-beispiel.de , die wir zweimal im Jahr veranstalten.
Aufgabenstellung
Wir haben ja die beiden Produkte Laufbahnwechsel.de und die Merivon, für die bereits jeweils ein separtes Logo besteht! Diese finden Sie im Anhang! Beide werden doch jedoch von einem Unternehmen, der KVL GmbH betrieben! Aktuell nutzen wir eine Visitenkarte mit dem Logo von KVL und eine mit dem Logo der MERIVON. Gerade im Hinblick darauf, dass wir zukünftig auch weiter Plattformen in unser Portfolio aufnehmen, möchte ich hier unsere V-Karten flexibler gestalten!
Ziel soll es also sein, eine Visitenkarte zu gestalten, auf dem klar wird, dass der Mitarbeiter von der KVL GmbH kommt, die KVL GmbH aber unterschiedliche Produkte betreibt.
Im Anhang finden Sie:
1. Das Logo von KVL
2. Das Logo von Merivon
3. Die aktuelle V-Karte von KVL
4. Die aktuelle V-Karte von MERIVON
Vielleicht ein kleiner Anreiz: Aktuell nutzen wir auch zwei getrennte Geschäftspapiere. Das von www.laufbahnwechsel-beispiel.de lade ich einmal hoch! Der Designer, der auch die Visitenkarte erstellt, erhällt im Anschluss den 1:1 Auftrag in Höhe von 200 Euro für die Erstellung des Geschäftspapiers! Wenn Sie jetzt schon einen Vorschlag für das Geschäftspapier einreichen, erhöht das natürlich Ihre Chancen, wobei ich verspreche, dass wir im Falle eine Annahme das 1:1 im Anschluß dennoch starten werden!

```html
<!DOCTYPE html>
<html lang="de">
<head>
<meta charset="utf-8">
<title>KVL GmbH – Visitenkarten</title>
<link href="https://fonts.googleapis.com/css2?family=Arimo:wght@400;700&display=swap" rel="stylesheet">
<style>
  :root{
    --stage:#d9dcdf;
    --paper:#ededed;
    --ink:#2b2b2b;
    --night:#1e1e1e;
    --navy:#1d4a92;
    --steel:#8a8a8a;
    --field:#3d6128;
    --camo-a:#6f7a3e;
    --camo-b:#4e5a2c;
    --camo-c:#8a6a3a;
  }
  *{box-sizing:border-box;margin:0;padding:0}
  html,body{width:1200px;height:900px;overflow:hidden}
  body{background:var(--stage);font-family:"Arimo",Arial,sans-serif;color:var(--ink)}
  .sheet{position:relative;width:1200px;height:900px;display:grid;
    grid-template-columns:520px 520px;grid-template-rows:336px 336px;
    gap:48px 56px;justify-content:center;align-content:center}
  .card{position:relative;overflow:hidden;box-shadow:0 6px 18px rgba(0,0,0,.22)}
  .card--camo{background:linear-gradient(135deg,var(--camo-a) 0%,var(--camo-b) 40%,var(--camo-c) 70%,var(--camo-b) 100%)}
  .card--night{background:var(--night)}
  .card--paper{background:var(--paper)}
  .rule{position:absolute;left:0;right:0;top:178px;height:7px}
  .rule::before,.rule::after{content:"";position:absolute;left:0;right:0;height:2px}
  .rule::before{top:0;background:var(--navy)}
  .rule::after{top:5px;background:var(--steel)}
  .brandset{position:absolute;left:0;right:0;top:80px;text-align:center}
  .brand-main{display:inline-flex;align-items:center;gap:10px;font-size:34px;font-weight:700;color:var(--navy)}
  .brand-main .dot{width:18px;height:18px;border-radius:50%;background:var(--navy)}
  .brand-sub{display:block;margin-top:118px;font-size:24px;font-weight:700;color:var(--field)}
  .card--night .brand-main{color:#e4e4e4}
  .card--night .brand-main .dot{background:var(--navy)}
  .card--camo .brand-main{color:#f2f2f2}
  .card--camo .brand-sub{color:#e8eedc}

  /* front with contact details */
  .front .person{position:absolute;left:26px;top:26px}
  .person-name{font-size:28px;color:var(--navy)}
  .person-role{font-size:13px;color:#555;margin-top:2px}
  .front .rule{top:92px;right:190px}
  .company{position:absolute;left:26px;top:114px;font-size:13px;line-height:1.4}
  .company strong{font-weight:700}
  .contact{position:absolute;left:26px;top:178px;font-size:12.5px;line-height:1.55;border-collapse:collapse}
  .contact th{font-weight:400;color:var(--navy);text-align:left;padding-right:18px}
  .contact td{color:var(--ink)}
  .side{position:absolute;right:20px;top:36px;width:170px;text-align:center}
  .side-brand{display:inline-flex;align-items:center;gap:6px;font-size:15px;font-weight:700;color:var(--navy)}
  .side-brand .dot{width:10px;height:10px;border-radius:50%;background:var(--navy)}
  .side-company{font-size:17px;font-weight:700;margin-top:12px;color:var(--ink)}
  .side-sub{font-size:15px;font-weight:700;color:var(--field);margin-top:16px}
  .side-domain{font-size:14px;font-weight:700;color:var(--field);margin-top:8px}
  .side-note{font-size:10px;font-weight:700;color:var(--ink);margin-top:4px}
  .band{position:absolute;left:0;right:0;bottom:0;height:30px;
    background:linear-gradient(90deg,var(--field) 0%,#2d5a5a 55%,var(--navy) 100%);
    display:flex;justify-content:space-between;align-items:center;padding:0 18px;
    font-size:13px;font-weight:700;color:#fff}
</style>
</head>
<body>
<main class="sheet">

  <section class="card card--camo" role="img" aria-label="Kartenrückseite mit Tarnmuster in Oliv-, Grün- und Brauntönen">
    <div class="rule"></div>
    <div class="brandset">
      <span class="brand-main"><span class="dot"></span>Laufbahnwechsel</span>
      <span class="brand-sub">MERIVON</span>
    </div>
  </section>

  <section class="card card--night">
    <div class="rule"></div>
    <div class="brandset">
      <span class="brand-main"><span class="dot"></span>Laufbahnwechsel</span>
      <span class="brand-sub">MERIVON</span>
    </div>
  </section>

  <section class="card card--paper">
    <div class="rule"></div>
    <div class="brandset">
      <span class="brand-main"><span class="dot"></span>Laufbahnwechsel</span>
      <span class="brand-sub">MERIVON</span>
    </div>
  </section>

  <section class="card card--paper front">
    <div class="person">
      <div class="person-name">Jonas Berger</div>
      <div class="person-role">Geschäftsführer</div>
    </div>
    <div class="rule"></div>
    <address class="company" style="font-style:normal">
      <strong>KVL GMBH</strong><br>
      Lindenweg 14<br>
      86999 Musterfeld
    </address>
    <table class="contact">
      <tr><th>Telefon.:</th><td>08100 - 555 20 17</td></tr>
      <tr><th>Mobil.:</th><td>0170 - 555 31 942</td></tr>
      <tr><th>E.:</th><td>jonas.berger@laufbahnwechsel-beispiel.de</td></tr>
      <tr><th>E.:</th><td>jonas.berger@merivon-beispiel.de</td></tr>
    </table>
    <div class="side">
      <span class="side-brand"><span class="dot"></span>Laufbahnwechsel</span>
      <div class="side-company">KVL GmbH</div>
      <div class="side-sub">MERIVON</div>
      <div class="side-domain">Merivon.de</div>
      <div class="side-note">ist eine Marke der KVL GmbH</div>
    </div>
    <div class="band">
      <span>www.merivon-beispiel.de</span>
      <span>www.laufbahnwechsel-beispiel.de</span>
    </div>
  </section>

</main>
</body>
</html>
```